cryotherapy business . Whole Body Cryotherapy, Localised Cryotherapy, Cryofacials

Need home page plus services, about, pricing, online booking, contact and blog page

I want something slick, hip and professional. Our studio colours are duck egg blue, white and grey

I would also like a social media scroll at the bottom of every page

I will upload some web designs that I like the look of

Target Market(s)

Men and Women 25-45

Industry/Entity Type

Health And Wellness

Coding

Coded - Design and coding required

Number of Pages Required

5+ page

Font styles to use
Serif
Sans Serif

Requirements
Must have
• Must be eye catching and easy to navigate
Nice to have
• animation
Should not have
• Not sure what the site should not have. I am fairly open to ideas as this is a brand new business.

```html
<!DOCTYPE html>
<html lang="en">
<head>
<meta charset="utf-8">
<title>Frostline – Cryotherapy Studio</title>
<link rel="stylesheet" href="https://fonts.googleapis.com/css2?family=Montserrat:wght@300;400;700;800&family=Roboto:ital,wght@0,400;0,500;0,700;1,400&display=swap">
<style>
:root{
  --blue:#1d3b8e;
  --blue-deep:#16307a;
  --blue-mid:#2a56a8;
  --ink:#222;
  --text:#444;
  --grey-band:#eceef1;
  --grey-light:#f4f5f7;
  --footer:#101114;
  --logo-grey:#a7a9ad;
  --white:#fff;
}
*{box-sizing:border-box;margin:0;padding:0}
html,body{width:1200px;height:3642px;overflow:hidden}
body{position:relative;background:var(--white);font-family:"Roboto",sans-serif;color:var(--text)}
.abs{position:absolute}
.topline{left:0;top:0;width:1200px;height:3px;background:var(--blue)}
.logo{font-family:"Montserrat",sans-serif;font-weight:400;letter-spacing:5px;color:var(--logo-grey)}
.site-logo{left:154px;top:42px;font-size:36px}
.call{left:878px;top:24px}
.call svg{position:absolute;left:0;top:4px}
.call small{position:absolute;left:38px;top:0;font-size:10px;font-weight:700;color:var(--blue);white-space:nowrap}
.call strong{position:absolute;left:36px;top:14px;font-size:20px;font-weight:700;color:var(--ink);white-space:nowrap}
.nav{right:154px;top:86px;display:flex;gap:24px;font-size:13px;font-weight:700;color:var(--ink)}
.hero{left:0;top:120px;width:1200px;height:660px;background:linear-gradient(115deg,#6d7f99 0%,#9fb0c6 30%,#c8b5a8 60%,#e6c3ad 85%,#d6a98c 100%)}
.hero-title{left:155px;top:262px;font-family:"Montserrat",sans-serif;font-weight:800;font-size:54px;line-height:65px;color:var(--white)}
.btn{display:flex;align-items:center;justify-content:center;border-radius:24px;font-weight:700;font-size:14px;color:var(--white);background:var(--blue)}
.hero-book{left:157px;top:482px;width:147px;height:44px}
.hero-more{left:326px;top:482px;width:162px;height:44px;background:none;border:2px solid var(--white)}
.slide-arrow{top:349px;width:37px;height:62px;display:flex;align-items:center;justify-content:center}
.hero-wave{left:0;top:640px}
.about-photo{left:137px;top:869px;width:354px;height:354px;border-radius:50%;border:3px solid var(--blue);background:radial-gradient(circle at 50% 55%,#9aa3b3 0%,#56627e 45%,#1f3f9a 100%)}
.h2{font-family:"Montserrat",sans-serif;font-weight:800;color:var(--blue);font-size:30px}
.about-title{left:544px;top:868px}
.about-text{left:544px;top:918px;width:499px;font-size:14.5px;line-height:30px;text-align:justify}
.about-text p+p{margin-top:10px}
.about-btn{left:544px;top:1182px;width:140px;height:44px}
.services-band{left:0;top:1300px}
.services-title{left:0;top:1470px;width:1200px;text-align:center}
.services-text{left:220px;top:1522px;width:760px;text-align:center;font-size:14.5px;line-height:28px;color:#333}
.svc{border-radius:50%;display:flex;flex-direction:column;align-items:center;justify-content:center;text-align:center;color:var(--white);box-shadow:0 6px 18px rgba(0,0,0,.18)}
.svc-body{left:137px;top:1648px;width:320px;height:320px;background:radial-gradient(circle at 50% 40%,#5a6ab0 0%,#7c8398 50%,#b8bcc4 100%);justify-content:flex-end;padding-bottom:58px}
.svc-local{left:442px;top:1645px;width:326px;height:326px;background:var(--blue)}
.svc-face{left:745px;top:1648px;width:320px;height:320px;background:linear-gradient(160deg,#1a2c63 0%,#3c4f86 40%,#c8a58c 65%,#6b6f78 100%);justify-content:flex-end;padding-bottom:50px}
.svc h3{font-family:"Roboto",sans-serif;font-weight:500;font-size:18px;line-height:26px}
.svc p{font-size:14px;line-height:23px;margin:10px 0 16px;width:210px}
.svc .outline{width:120px;height:36px;border:2px solid var(--white);border-radius:20px;display:flex;align-items:center;justify-content:center;font-weight:700;font-size:14px}
.pricing-title{left:0;top:2070px;width:1200px;text-align:center}
.pricing-sub{left:0;top:2118px;width:1200px;text-align:center;font-size:14px;line-height:27px;color:#333}
.card{top:2216px;height:399px;background:var(--white);border:1px solid #e2e3e6;box-shadow:0 2px 6px rgba(0,0,0,.06);text-align:center}
.card h4{margin-top:36px;font-size:14px;font-weight:400;color:var(--ink)}
.price{margin-top:14px;font-family:"Montserrat",sans-serif;font-weight:800;color:#333;font-size:44px;line-height:46px}
.price sup{font-size:24px;font-weight:400;vertical-align:18px}
.card .per{font-size:10px;color:#555}
.card hr{border:0;border-top:1px solid #ddd;margin:26px 30px 22px}
.rows{font-size:15px;line-height:39px;color:#333}
.rows span{display:inline-block}
.rows .k{width:80px;text-align:left}
.rows .d{width:30px}
.rows .v{width:40px;text-align:left}
.card .btn{width:118px;height:42px;margin:18px auto 0}
.card-mid{box-shadow:0 6px 16px rgba(0,0,0,.1);border:none}
.card-mid .price{color:var(--blue);font-size:56px;line-height:58px}
.card-mid .price sup{color:var(--blue);font-size:30px}
.mid-bar{left:462px;top:2626px;width:280px;height:6px;background:var(--blue)}
.reviews-band{left:0;top:2730px}
.reviews-title{left:0;top:2890px;width:1200px;text-align:center}
.review{top:2964px;width:272px;height:150px;background:var(--white);border-radius:8px;box-shadow:0 4px 14px rgba(0,0,0,.08);padding:20px 18px}
.review .avatar{position:absolute;left:18px;top:20px;width:38px;height:38px;border-radius:50%;background:#c9cbd0}
.review .name{position:absolute;left:76px;top:20px;font-size:13.5px;color:var(--ink)}
.review .stars{position:absolute;left:76px;top:39px;font-size:11px;color:#e8a800;white-space:nowrap}
.review .stars em{font-style:normal;color:#b8b8b8;margin-left:3px}
.review p{position:absolute;left:18px;top:78px;width:240px;font-size:11.5px;line-height:20px;font-style:italic;color:#666}
.rev-arrow{top:3030px}
.footer{left:0;top:3200px}
.foot-logo{left:154px;top:3320px;font-size:32px;color:#c6c8cc}
.field{left:157px;width:219px;height:26px;border:1px solid #9a9ca0;font-size:9px;color:#ddd;padding:6px 8px}
.send{left:157px;top:3500px;width:130px;height:32px;font-size:11px}
.fcol{top:3328px;color:#d6d7da;font-size:14px}
.fcol h5{font-weight:400;font-size:17px;color:#e9eaec;margin-bottom:18px}
.fitem{position:relative;padding-left:24px;line-height:22px;margin-bottom:11px}
.fitem svg{position:absolute;left:0;top:4px}
.social{display:flex;align-items:center;gap:16px;margin-bottom:22px}
.social i{width:30px;height:30px;border-radius:50%;display:block;background:var(--blue-mid)}
.foot-rule{left:154px;top:3573px;width:889px;height:1px;background:#4a4c52}
.copyright{left:0;top:3601px;width:1200px;text-align:center;font-size:12.5px;color:#cfd0d3}
</style>
</head>
<body>
<div class="abs topline"></div>
<div class="abs logo site-logo">FROSTLINE</div>
<div class="abs call">
  <svg width="26" height="30" viewBox="0 0 24 24"><path fill="#1d3b8e" d="M6.6 10.8c1.4 2.8 3.8 5.1 6.6 6.6l2.2-2.2c.3-.3.7-.4 1-.2 1.1.4 2.3.6 3.6.6.6 0 1 .4 1 1V20c0 .6-.4 1-1 1C10.6 21 3 13.4 3 4c0-.6.4-1 1-1h3.5c.6 0 1 .4 1 1 0 1.3.2 2.5.6 3.6.1.3 0 .7-.2 1z"/></svg>
  <small>CALL US TODAY</small>
  <strong>555-014-2290</strong>
</div>
<nav class="abs nav"><span>HOME</span><span>SERVICES</span><span>ABOUT</span><span>PRICING</span><span>ONLINE BOOKING</span><span>CONTACT &amp; BLOG</span></nav>

<section class="abs hero" role="img" aria-label="Photo of a woman relaxing with closed eyes during a cryofacial treatment with cold vapour"></section>
<h1 class="abs hero-title">OPTIMAL<br>PERFORMANCE<br>AND RECOVERY</h1>
<div class="abs btn hero-book">BOOK NOW</div>
<div class="abs btn hero-more">VIEW MORE</div>
<div class="abs slide-arrow" style="left:0;background:#fff"><svg width="12" height="18" viewBox="0 0 12 18"><path d="M10 2 3 9l7 7" fill="none" stroke="#1d3b8e" stroke-width="2.5"/></svg></div>
<div class="abs slide-arrow" style="left:1163px;background:#1d3b8e"><svg width="12" height="18" viewBox="0 0 12 18"><path d="M2 2l7 7-7 7" fill="none" stroke="#fff" stroke-width="2.5"/></svg></div>
<svg class="abs hero-wave" width="1200" height="150" viewBox="0 0 1200 150">
  <path d="M0 22 C300 110 500 126 640 120 C820 112 1000 70 1200 -10 L1200 150 L0 150Z" fill="#fff"/>
  <path d="M198 72 C380 130 520 140 620 135 C780 128 900 100 1003 72 C880 112 760 140 610 138 C470 136 340 114 198 72Z" fill="#1d3b8e"/>
</svg>

<div class="abs about-photo" role="img" aria-label="Photo of a client standing inside a whole body cryotherapy chamber"></div>
<h2 class="abs h2 about-title">ABOUT CRYOTHERAPY</h2>
<div class="abs about-text">
  <p>Originally invented by doctors as a powerful anti-inflammatory tool, cryo therapy is a quick, noninvasive process that exposes your body to extreme cold of up to -250°F.</p>
  <p>This sudden drop in temperature increases circulation and pumps reoxygen ated and nutrient enriched blood back into the bloodstream reducing pain &amp; inflammation and alleviating sore muscles. It’s also known to release ‘feel good’ endorphins that help improve sleep, reduce stress, and increase your metabolism.</p>
</div>
<div class="abs btn about-btn">READ MORE</div>

<svg class="abs services-band" width="1200" height="510" viewBox="0 0 1200 510" role="img" aria-label="Soft grey background with cold mist">
  <defs><linearGradient id="mist" x1="0" y1="0" x2="1" y2="1"><stop offset="0" stop-color="#e4e7ec"/><stop offset=".5" stop-color="#f1f2f5"/><stop offset="1" stop-color="#e2e5ea"/></linearGradient></defs>
  <path d="M0 120 C120 150 260 100 450 50 C600 10 720 -5 860 30 C1000 65 1120 130 1200 200 L1200 500 L0 500Z" fill="url(#mist)"/>
  <path d="M0 122 C120 152 260 102 450 52 C600 12 720 -3 860 32 C1000 67 1120 132 1200 202" fill="none" stroke="#1d3b8e" stroke-width="5"/>
</svg>
<h2 class="abs h2 services-title">OUR SERVICES</h2>
<p class="abs services-text">This sudden drop in temperature increases circulation and pumps reoxygen ated and nutrient enriched blood back into the bloodstream reducing pain &amp; inflammation and alleviating sore muscles. It’s also known to release ‘feel good’ endorphins that help improve sleep, reduce stress, and increase your metabolism.</p>
<div class="abs svc svc-body" role="img" aria-label="Photo of a woman in a whole body cryotherapy chamber"><h3>WHOLE BODY<br>CRYOTHERAPY</h3></div>
<div class="abs svc svc-face" role="img" aria-label="Photo of a woman receiving a cryofacial"><h3 style="font-weight:700">CRYOFACIALS</h3></div>
<div class="abs svc svc-local"><h3>LOCALISED<br>CRYOTHERAPY</h3><p>Dolor utan quam venenatis nec euismod sit amet consectur</p><div class="outline">READ MORE</div></div>

<h2 class="abs h2 pricing-title">OUR PRICING</h2>
<p class="abs pricing-sub">Sed ut perspiciatis unde omnis iste natus consequuntur magni volupt<br>satemac cusantium doloremque ratione sit</p>
<div class="abs card" style="left:155px;width:282px">
  <h4>Whole Body Cryotherapy</h4>
  <div class="price"><sup>$</sup>400</div><div class="per">Monthly</div>
  <hr>
  <div class="rows"><div><span class="k">SINGLE</span><span class="d">-</span><span class="v">$40</span></div><div><span class="k">10 PACK</span><span class="d">-</span><span class="v">$380</span></div><div><span class="k">20 PACK</span><span class="d">-</span><span class="v">$720</span></div></div>
  <div class="btn">BOOK NOW</div>
</div>
<div class="abs card card-mid" style="left:462px;width:280px">
  <h4>Local Cryotherapy</h4>
  <div class="price" style="margin-top:8px"><sup>$</sup>400</div><div class="per">Monthly</div>
  <hr style="margin-top:18px">
  <div class="rows"><div><span class="k">SINGLE</span><span class="d">-</span><span class="v">$40</span></div><div><span class="k">10 PACK</span><span class="d">-</span><span class="v">$380</span></div><div><span class="k">20 PACK</span><span class="d">-</span><span class="v">$720</span></div></div>
  <div class="btn">BOOK NOW</div>
</div>
<div class="abs mid-bar"></div>
<div class="abs card" style="left:762px;width:282px">
  <h4>Cryo Facial</h4>
  <div class="price"><sup>$</sup>400</div><div class="per">Monthly</div>
  <hr>
  <div class="rows"><div><span class="k">SINGLE</span><span class="d">-</span><span class="v">$40</span></div><div><span class="k">10 PACK</span><span class="d">-</span><span class="v">$380</span></div><div><span class="k">20 PACK</span><span class="d">-</span><span class="v">$720</span></div></div>
  <div class="btn">BOOK NOW</div>
</div>

<svg class="abs reviews-band" width="1200" height="520" viewBox="0 0 1200 520">
  <path d="M0 45 C200 15 420 50 620 40 C820 30 1000 0 1200 20 L1200 520 L0 520Z" fill="#f1f2f4"/>
</svg>
<h2 class="abs h2 reviews-title">CLIENT REVIEWS</h2>
<svg class="abs rev-arrow" style="left:116px" width="16" height="26" viewBox="0 0 16 26"><path d="M13 3 4 13l9 10" fill="none" stroke="#1d3b8e" stroke-width="4"/></svg>
<svg class="abs rev-arrow" style="left:1085px" width="16" height="26" viewBox="0 0 16 26"><path d="M3 3l9 10-9 10" fill="none" stroke="#1d3b8e" stroke-width="4"/></svg>
<div class="abs review" style="left:164px"><i class="avatar"></i><span class="name">Mira, 2/9/2019</span><span class="stars">★★★★★<em>(Westbrook Clients)</em></span><p>Lorem ipsum dolor sit amet, consectetur do adipisc ing elit, sed do eiusmod temporaos incididunt utaus labore et dolore.</p></div>
<div class="abs review" style="left:472px"><i class="avatar"></i><span class="name">Elena.R, 2/9/2019</span><span class="stars">★★★★★<em>(Eastfield Clients)</em></span><p>Lorem ipsum dolor sit amet, consectetur do adipisc ing elit, sed do eiusmod temporaos incididunt utaus labore et dolore.</p></div>
<div class="abs review" style="left:780px"><i class="avatar"></i><span class="name">Joanna.K, 2/9/2019</span><span class="stars">★★★★★<em>(Westbrook Clients)</em></span><p>Lorem ipsum dolor sit amet, consectetur do adipisc ing elit, sed do eiusmod temporaos incididunt utaus labore et dolore.</p></div>

<svg class="abs footer" width="1200" height="442" viewBox="0 0 1200 442">
  <path d="M0 70 C200 30 420 10 620 12 C820 14 1020 50 1200 110 L1200 442 L0 442Z" fill="#101114"/>
  <path d="M0 70 C200 30 420 10 620 12 C820 14 1020 50 1200 110" fill="none" stroke="#2a56a8" stroke-width="9"/>
  <path d="M0 50 C200 14 420 -4 620 0 C820 4 1020 36 1200 90" fill="none" stroke="#1d3b8e" stroke-width="4"/>
</svg>
<div class="abs logo foot-logo">FROSTLINE</div>
<div class="abs field" style="top:3372px">Full Name</div>
<div class="abs field" style="top:3407px">Email</div>
<div class="abs field" style="top:3442px;height:42px">Message</div>
<div class="abs btn send">SEND MESSAGE</div>

<div class="abs fcol" style="left:431px;width:240px">
  <h5>Contact 1</h5>
  <div class="fitem"><svg width="10" height="14" viewBox="0 0 10 14"><path d="M5 0a5 5 0 0 0-5 5c0 4 5 9 5 9s5-5 5-9a5 5 0 0 0-5-5zm0 7a2 2 0 1 1 0-4 2 2 0 0 1 0 4z" fill="#d6d7da"/></svg>2nd Floor, 18 Harbor Lane,<br>WESTBROOK.</div>
  <div class="fitem"><svg width="13" height="10" viewBox="0 0 13 10"><rect x=".5" y=".5" width="12" height="9" fill="none" stroke="#d6d7da"/><path d="M.5.5l6 5 6-5" fill="none" stroke="#d6d7da"/></svg>hello@frostline.example</div>
  <div class="fitem"><svg width="12" height="12" viewBox="0 0 24 24"><path fill="#d6d7da" d="M6.6 10.8c1.4 2.8 3.8 5.1 6.6 6.6l2.2-2.2c.3-.3.7-.4 1-.2 1.1.4 2.3.6 3.6.6.6 0 1 .4 1 1V20c0 .6-.4 1-1 1C10.6 21 3 13.4 3 4c0-.6.4-1 1-1h3.5c.6 0 1 .4 1 1 0 1.3.2 2.5.6 3.6.1.3 0 .7-.2 1z"/></svg>555-014-2290</div>
  <div class="fitem"><svg width="12" height="12" viewBox="0 0 12 12"><circle cx="6" cy="6" r="5.2" fill="none" stroke="#d6d7da" stroke-width="1.4"/><path d="M6 3v3h2.5" fill="none" stroke="#d6d7da" stroke-width="1.4"/></svg>Mon - Fri &nbsp;: 6:30 am - 8:00 pm<br>&nbsp;Sat &nbsp;- Sun : Closed</div>
</div>
<div class="abs fcol" style="left:684px;width:240px">
  <h5>Contact 2</h5>
  <div class="fitem"><svg width="10" height="14" viewBox="0 0 10 14"><path d="M5 0a5 5 0 0 0-5 5c0 4 5 9 5 9s5-5 5-9a5 5 0 0 0-5-5zm0 7a2 2 0 1 1 0-4 2 2 0 0 1 0 4z" fill="#d6d7da"/></svg>Ironleaf Works,<br>Lorem Ipsum.</div>
  <div class="fitem"><svg width="13" height="10" viewBox="0 0 13 10"><rect x=".5" y=".5" width="12" height="9" fill="none" stroke="#d6d7da"/><path d="M.5.5l6 5 6-5" fill="none" stroke="#d6d7da"/></svg>hello@frostline.example</div>
  <div class="fitem"><svg width="12" height="12" viewBox="0 0 24 24"><path fill="#d6d7da" d="M6.6 10.8c1.4 2.8 3.8 5.1 6.6 6.6l2.2-2.2c.3-.3.7-.4 1-.2 1.1.4 2.3.6 3.6.6.6 0 1 .4 1 1V20c0 .6-.4 1-1 1C10.6 21 3 13.4 3 4c0-.6.4-1 1-1h3.5c.6 0 1 .4 1 1 0 1.3.2 2.5.6 3.6.1.3 0 .7-.2 1z"/></svg>555-014-2290</div>
  <div class="fitem"><svg width="12" height="12" viewBox="0 0 12 12"><circle cx="6" cy="6" r="5.2" fill="none" stroke="#d6d7da" stroke-width="1.4"/><path d="M6 3v3h2.5" fill="none" stroke="#d6d7da" stroke-width="1.4"/></svg>Mon - Fri &nbsp;: 6:00 am - 7:00 pm<br>&nbsp;Sat &nbsp;- Sun : Closed</div>
</div>
<div class="abs fcol" style="left:933px;width:140px">
  <h5>Follow Us On</h5>
  <div class="social"><i></i>Circlepost</div>
  <div class="social"><i></i>Snapwall</div>
  <div class="social"><i></i>Chirpline</div>
</div>
<div class="abs foot-rule"></div>
<p class="abs copyright">Copyright © 2019. All Rights Reserved.</p>
</body>
</html>
```